Etiketten für Imkerei mit Spezialisierung auf Bio Lagenhonig
Zielgruppe
wiesfalter.at - BioImkerei Lindorf
Kleine Nebenerwerbs Imkerei mit Spezialisierung auf Bio Lagenhonig (nähere Infos sind auf der Website nachzulesen)
Als weitere Produktlinie bieten wir Honig+ / Honig mit Zutaten wie Himbeer, Erdbeer, Haselnuss, Mohn, Ingwer, Thymian, usw an.
Zielgruppe: Personen die offen für die Vielfalt der Natur sind, gesunde und natürliche Lebensmittel lieben und die bereit sind die aufwändige, großteils manuelle, Arbeit entsprechend zu entlohnen.
Gesucht:
ÄNDERUNG: Da die Anforderung für das ausgesetzte Preisgeld offensichtlich zu komplex ist, reduziere ich die Anforderung auf Etiketten für die Produktserie Honig+, Gesamtkonzepte sind nicht erforderlich werden aber gerne angenommen.
ÜRSPRÜNGLICH:
Redesign der aktuellen Honigetiketten
Basisdesign für Lagenhonig und Honig+ das entsprechende Varianten zulässt.
Aufgabenstellung
Ich wünsche mir ein modernes, edles (oder Öko look) Design mit sehr guten Wiedererkennungswert das sich von gängigen Honigetiketten deutlich abhebt.
Das wiesfalter Logo soll enthalten sein kann aber bei Bedarf angepasst werden (z.B. monocrome Verison)
Für Lagenhonig werden derzeit 400g und 100g Gläser mit hohem schwarzen DrehKap Decke und,
für Honig+ 250g und 100g mit hohem silbenen DrehKap Deckel verwendet. Beispiele sind im Webshop unter https://solvenhof.at/index.php/wiesfalter ersichtilich.
Für das Ablaufdatum ist evtl. ein Feld für manuelle Stempelung vorzusehen.
Bitte die Sichtfeldregelung der EU Verpackungsverordnung einhalten.
Bisherige Etiketten hatten den Anspruch das diese auf guten Laserdruckern ausdruckbar waren - das ist jetzt nicht mehr zwingend notwendig (wäre für Kleinauflagen aber trotzdem vorteilhaft)

```html
<!DOCTYPE html>
<html lang="de">
<head>
<meta charset="utf-8">
<title>Honig Etikett – Bio Imkerei Lindorf</title>
<link href="https://fonts.googleapis.com/css2?family=Source+Sans+3:wght@300;400;600&family=Montserrat:wght@700&display=swap" rel="stylesheet">
<style>
  :root {
    --page: #ffffff;
    --honey-light: #fbc62a;
    --honey: #f6b414;
    --honey-deep: #ef9a12;
    --label-white: #ffffff;
    --ink-grey: #8a8a8a;
    --ink-dark: #333333;
    --bio-green: #b7d35a;
    --stamp: #ececec;
    --line: rgba(255,255,255,0.85);
  }
  * { margin: 0; padding: 0; box-sizing: border-box; }
  html, body { width: 1180px; height: 1200px; overflow: hidden; background: var(--page); }
  body { font-family: "Source Sans 3", sans-serif; position: relative; }

  .label {
    position: absolute; left: 40px; top: 330px; width: 1100px; height: 540px;
    background: linear-gradient(180deg, var(--honey-light) 0%, var(--honey) 70%, var(--honey-deep) 100%);
  }

  .info-panel {
    position: absolute; left: 0; top: 70px; width: 240px; height: 466px;
    background: var(--label-white); padding: 56px 18px 0 24px; color: var(--ink-grey);
  }
  .info-panel .variety { font-size: 16px; line-height: 22px; }
  .info-panel .origin { font-size: 12px; margin-top: 44px; }
  .info-panel .control { position: absolute; left: 24px; bottom: 130px; font-size: 18px; }
  .info-panel .control small { display: block; font-size: 14px; font-weight: 300; }
  .bio-mark {
    position: absolute; left: 24px; bottom: 76px; width: 64px; height: 46px;
    background: var(--bio-green); border-radius: 4px;
  }
  .info-panel .weight { position: absolute; left: 24px; bottom: 30px; font-size: 28px; font-weight: 300; }

  .producer { position: absolute; left: 290px; top: 180px; color: var(--label-white); }
  .producer .name { font-size: 26px; font-weight: 600; }
  .producer .address { font-size: 21px; font-weight: 300; line-height: 27px; }
  .producer .web { font-family: "Montserrat", sans-serif; font-size: 22px; margin-top: 26px; letter-spacing: 0.5px; }

  .best-before { position: absolute; left: 290px; top: 475px; color: var(--label-white); font-size: 17px; line-height: 21px; font-weight: 300; }
  .stamp-field { position: absolute; left: 400px; top: 450px; width: 250px; height: 88px; }
  .stamp-field span {
    position: absolute; left: 0; right: 0; top: 44px; text-align: center;
    font-size: 21px; color: var(--ink-dark);
  }

  .brand-panel { position: absolute; left: 760px; top: 80px; width: 300px; height: 460px; color: var(--label-white); }
  .brand-panel .product { font-size: 32px; font-weight: 600; letter-spacing: 2px; text-align: center; }
  .brand-panel .rule { height: 2px; background: var(--line); margin: 16px 0; }
  .brand-panel .wordmark {
    display: block; width: 240px; height: 130px; margin: 40px auto 0;
    background: linear-gradient(135deg, rgba(255,255,255,0.55), rgba(255,255,255,0.2)); border-radius: 6px;
  }
  .brand-panel .subtitle { font-size: 28px; font-weight: 300; text-align: center; margin-top: 12px; }
  .brand-panel .rule.bottom { margin-top: 110px; }
  .brand-panel .web-small { font-size: 19px; font-weight: 300; text-align: center; }
</style>
</head>
<body>
  <section class="label">
    <div class="info-panel">
      <p class="variety">Blütenhonig<br>Kaltschleuderung</p>
      <p class="origin">Herkunft: Österreich</p>
      <p class="control">AT-BIO-917<small>EU-Landwirtschaft</small></p>
      <div class="bio-mark" role="img" aria-label="Bio-Siegel"></div>
      <p class="weight">400 g</p>
    </div>

    <div class="producer">
      <p class="name">Bio Imkerei Lindorf</p>
      <p class="address">Lindenweg 24<br>3580 Hollenbach</p>
      <p class="web">www.wiesfalter.at</p>
    </div>

    <p class="best-before">Mindestens<br>haltbar bis:</p>
    <div class="stamp-field">
      <svg width="250" height="88" viewBox="0 0 250 88"><path d="M0 88 A125 88 0 0 1 250 88 Z" fill="var(--stamp)"/></svg>
      <span>30.06.2019</span>
    </div>

    <div class="brand-panel">
      <p class="product">HONIG</p>
      <div class="rule"></div>
      <span class="wordmark" role="img" aria-label="Handgeschriebener Schriftzug der Sorte"></span>
      <p class="subtitle">Feinste Ernte</p>
      <div class="rule bottom"></div>
      <p class="web-small">www.wiesfalter.at</p>
    </div>
  </section>
</body>
</html>
```